A specialised Sport management needs a corporate brochure design

We are a specialized company in the management and consultancy of sports events. and need to have a company brochure
We provide the following services;
Event management
Venues management
Production
Ticketing
Consulting
Hospitality
Activity management
Event timing
Branding of event
Event supplies
We need a corporate profile design for our company to showcase the major events that we have covered , with images, information, statistics, surveys, products and services used. We want to highlight our professionalism and execution of the events, experience of the participants, spectators . How we have grown in the past few years and reached the international standards.
Objectives of the work:
To get sponsors and partners for future business and to present Tri-Crest
as not just a sports management company but also a professional sports
events management company.
You can check our website
www.tri-crest.example
Target Market(s)
Sponsors and corporate partners
Industry/Entity Type
Events
Requirements
Must have
- Must Have:
- - Very professional look
- -Some event images,Event information, statistics, surveys, products and services used. We want to highlight our professionalism and execution of the events (Attached)
Nice to have
- Similar momentom of the below design
- http://www.lumavent.example/wp-content/themes/lumavent/pdf/CP-2014-15-V10-Web.pdf

```html
<!DOCTYPE html>
<html lang="en">
<head>
<meta charset="utf-8">
<title>Tri-Crest Corporate Brochure Spread</title>
<link rel="stylesheet" href="https://fonts.googleapis.com/css2?family=Quicksand:wght@400;500;700&display=swap">
<style>
  :root {
    --backdrop: #ececec;
    --paper: #ffffff;
    --orange: #e8692f;
    --orange-soft: #f4b48f;
    --green: #1f7a3d;
    --grey: #8c8c8c;
    --grey-light: #d9d9d9;
    --ink: #4a4a4a;
    --ink-soft: #7a7a7a;
    --photo-race: #5b6a82;
    --photo-race-2: #c9c2b8;
    --photo-gym: #6d8ea8;
    --photo-gym-2: #2b2b2b;
  }
  * { box-sizing: border-box; margin: 0; padding: 0; }
  html, body { width: 1200px; height: 799px; overflow: hidden; }
  body {
    background: var(--backdrop);
    font-family: "Quicksand", sans-serif;
    color: var(--ink);
    position: relative;
  }
  .spread {
    position: absolute;
    left: 50px; top: 140px;
    width: 1100px; height: 520px;
    display: flex;
    background: var(--paper);
    box-shadow: 0 20px 40px rgba(0,0,0,.15);
  }
  .page { position: relative; width: 550px; height: 100%; overflow: hidden; }
  .page--left { border-right: 1px solid var(--grey-light); }

  .brand {
    position: absolute;
    display: flex; align-items: center; gap: 6px;
    font-weight: 700; font-size: 17px; color: var(--orange);
  }
  .brand__dot { width: 14px; height: 14px; border-radius: 50%; background: var(--green); }
  .page--left .brand { right: 20px; top: 44px; }
  .page--right .brand { right: 30px; top: 24px; }

  .title-band {
    position: absolute; top: 130px; height: 34px;
    background: linear-gradient(90deg, rgba(232,105,47,.15), var(--orange));
    color: #fff; font-size: 20px; font-weight: 500;
    display: flex; align-items: center; padding: 0 18px;
  }
  .page--left .title-band { left: 210px; right: 0; justify-content: flex-end; }
  .page--right .title-band {
    left: 0; width: 340px;
    background: linear-gradient(90deg, var(--orange), rgba(232,105,47,.15));
  }

  .photo { position: absolute; }
  .photo--race {
    left: 0; top: 164px; width: 210px; height: 270px;
    background: linear-gradient(160deg, var(--photo-race-2), var(--photo-race) 60%, #2d3340);
  }
  .photo--gym {
    right: 0; top: 90px; width: 190px; height: 250px;
    background: linear-gradient(170deg, var(--photo-gym), #9aa3ab 45%, var(--photo-gym-2));
  }

  .copy { position: absolute; font-size: 9.5px; line-height: 1.7; }
  .about { left: 230px; top: 180px; width: 300px; text-align: center; }
  .about p + p { margin-top: 8px; }
  .about .signature { text-align: right; font-size: 8.5px; color: var(--ink-soft); }
  .goal { left: 230px; top: 275px; width: 300px; color: var(--orange); }
  .goal h2 { font-size: 17px; font-weight: 500; margin-bottom: 6px; }

  .segments { left: 24px; top: 178px; width: 320px; }
  .segments h3 { font-size: 10px; font-weight: 700; color: var(--ink); }
  .segments p { margin-bottom: 8px; }

  .bars { position: absolute; bottom: 56px; left: 0; right: 0; height: 12px; display: flex; }
  .bar--grey { background: var(--grey); }
  .bar--green { background: var(--green); }
  .bar--orange { background: var(--orange); }
  .sweep {
    position: absolute; left: 0; right: 0; bottom: 68px; height: 30px;
    background: linear-gradient(90deg, transparent, var(--grey-light));
  }
  .page--right .sweep { background: linear-gradient(90deg, var(--grey-light), transparent); }
</style>
</head>
<body>
  <main class="spread">
    <section class="page page--left">
      <div class="brand"><span class="brand__dot"></span>Tri-Crest</div>
      <div class="title-band">About Us</div>
      <div class="photo photo--race" role="img" aria-label="Photo of a racing car doing a burnout with tyre smoke"></div>
      <div class="copy about">
        <p>Tri-Crest is the leading company in the region which specialises in the management and consultancy of sports events, building on many years of industry experience. Tri-Crest has organised national and international events over the past years.</p>
        <p>To become the nation's most trusted partner for sporting events.</p>
        <p class="signature">Management Team</p>
      </div>
      <div class="copy goal">
        <h2>Our Goal</h2>
        <p>Raise awareness of sport practice and bring sporting events in line with international standards, allowing every individual to participate in different types of sport events held in town. Each year we get closer to our goal to promote active lifestyle and sports practice in the country, and to help our partners play a major role in that journey.</p>
      </div>
      <div class="sweep"></div>
      <div class="bars">
        <span class="bar--grey" style="width:150px"></span>
        <span class="bar--green" style="width:200px"></span>
        <span class="bar--orange" style="width:200px"></span>
      </div>
    </section>

    <section class="page page--right">
      <div class="brand"><span class="brand__dot"></span>Tri-Crest</div>
      <div class="title-band">Target Segment</div>
      <div class="photo photo--gym" role="img" aria-label="Photo of an athlete lifting a barbell overhead at a fitness competition with flags behind"></div>
      <div class="copy segments">
        <h3>Mainstream Public</h3>
        <p>The largest audience segment, predominantly youth and families, who enjoy fun and lively events. They are supported and attracted by the incredible range of sport events and promotion organised by our team, with attendance of over 20,000.</p>
        <h3>Engaged:</h3>
        <p>This segment concentrates all those who are engaged in sports and fitness but not necessarily in competitive events.</p>
        <h3>Athletes</h3>
        <p>Majority of athletes are ranging between 18 and 45 years old, 70% male and 30% female, with high disposable income. They are fit, motivated and looking to challenge themselves.</p>
      </div>
      <div class="sweep"></div>
      <div class="bars">
        <span class="bar--orange" style="width:230px"></span>
        <span class="bar--green" style="width:200px"></span>
        <span class="bar--grey" style="width:120px"></span>
      </div>
    </section>
  </main>
</body>
</html>
```